Multi-Line Insurance PPC Landing Page - Conversion optimized.

We have a PPC landing page used for the general population to get an insurance quote through an agent's site.

We'd like to improve the page for PPC traffic, make it more conversion friendly.

Site should be a single long page.

We will dynamically change the form and headlines on the page depending on what insurance "line" is being called. ie, Lift, Auto, Home, Business.

The enclosed AI file has all of the raw elements we need. We're looking to enhance the design and conversion ability.

Target Market(s)

General public needed insurance services.

Industry/Entity Type

Insurance Broker

Number of Pages Required

1 page

Font styles to use
Sans Serif

Requirements
Must have
• Form, agent picture, name, address.

```html
<!DOCTYPE html>
<html lang="en">
<head>
<meta charset="utf-8">
<title>Insurance Agent – Get an Instant Insurance Quote</title>
<link rel="stylesheet" href="https://fonts.googleapis.com/css2?family=Open+Sans:wght@400;600;700&family=Raleway:wght@500;600;700&display=swap">
<style>
:root{
  --blue:#1f5fae;
  --navy:#1b3f74;
  --ink:#333a44;
  --muted:#6b7380;
  --line:#d6dbe2;
  --field:#f4f6f8;
  --grey:#ececec;
  --white:#ffffff;
}
*{box-sizing:border-box;margin:0;padding:0}
html,body{width:1200px;height:2232px;overflow:hidden}
body{position:relative;background:var(--white);font-family:"Open Sans",Arial,sans-serif;color:var(--ink)}
.caps{font-family:"Raleway","Open Sans",sans-serif;font-variant:small-caps;letter-spacing:1px}

/* header */
.site-header{position:absolute;top:0;left:0;width:1200px;height:74px;display:flex;align-items:center;justify-content:space-between;padding:0 130px}
.brand{font-size:46px;font-weight:700;color:var(--navy)}
.brand span{color:var(--blue)}
.header-phone{display:flex;align-items:center;gap:10px;font-size:24px;font-weight:600;color:var(--navy)}

/* hero */
.hero{position:absolute;top:74px;left:0;width:1200px;height:400px;background:linear-gradient(180deg,#6f7f8d 0%,#4d5a66 45%,#2c333a 100%)}
.hero-band{position:absolute;left:0;bottom:50px;width:1200px;height:62px;background:rgba(15,30,50,.55);display:flex;align-items:center;justify-content:center;gap:60px}
.hero-band h1{font-size:26px;font-weight:700;color:var(--white);letter-spacing:1px}
.btn{display:inline-block;background:var(--blue);color:var(--white);font-weight:700;font-size:14px;letter-spacing:1px;padding:8px 20px;border-radius:2px}
.hero-band .btn{background:var(--white);color:var(--navy);font-size:16px}

/* quote card */
.quote-card{position:absolute;top:474px;left:130px;width:940px;height:360px;background:var(--white);box-shadow:0 2px 10px rgba(0,0,0,.18);display:flex}
.agent{width:250px;border-right:1px solid var(--line);padding:34px 24px;text-align:center}
.agent-photo{width:110px;height:130px;margin:0 auto 12px;background:linear-gradient(180deg,#b7c1cc,#3b4652)}
.agent-name{font-size:17px;font-weight:700;color:var(--blue)}
.agent-contact{font-size:13px;color:var(--ink);margin-top:8px;display:flex;align-items:center;justify-content:center;gap:6px}
.agent-note{font-size:12px;color:var(--muted);margin-top:12px;line-height:1.45}
.quote-form{flex:1;padding:24px 34px}
.quote-form h2{font-size:30px;color:var(--blue);text-align:center;font-weight:600}
.quote-form h2 b{color:var(--navy)}
.form-grid{display:grid;grid-template-columns:1fr 1fr;column-gap:30px;row-gap:8px;margin-top:18px}
.field label{display:block;font-size:12px;color:var(--muted);margin-bottom:3px}
.input{height:26px;border:1px solid var(--line);background:var(--field);font-size:12px;color:#9aa1ab;padding:4px 8px}
.dob{display:flex;gap:6px}.dob .input{flex:1}
.submit{margin-left:calc(50% + 15px);margin-top:12px;padding:8px 40px}

/* section headings */
.section-title{font-size:36px;font-weight:600;color:var(--navy);text-align:center}
.section-title span{color:var(--blue)}
.rule{width:60px;height:2px;background:var(--blue);margin:10px auto 0}

.about{position:absolute;top:880px;left:0;width:1200px;padding:0 130px;text-align:center}
.about p{margin-top:22px;font-size:14px;line-height:1.6;color:var(--muted)}

/* products */
.products{position:absolute;top:1090px;left:0;width:1200px}
.product-grid{display:flex;justify-content:center;gap:40px;margin-top:40px}
.product{width:200px;text-align:center}
.product svg{height:80px}
.product h3{margin-top:14px;font-size:18px;font-weight:600;color:var(--blue);letter-spacing:1px}
.product p{font-size:13px;color:var(--muted);line-height:1.45;margin:10px 0 14px}

/* testimonials */
.testimonials{position:absolute;top:1450px;left:0;width:1200px;height:360px;background:var(--grey);padding-top:36px}
.people{position:relative;margin-top:30px;height:230px}
.person{position:absolute;border-radius:50%;background:radial-gradient(circle,#c8a58c 0%,#8d6e5c 100%)}
.person.side{top:30px;width:140px;height:140px;background:radial-gradient(circle,#d8d8d8 0%,#9a9a9a 100%);opacity:.85}
.person.left{left:180px}.person.right{right:180px}
.person.main{left:525px;top:0;width:150px;height:150px;border:5px solid var(--white)}
.quote-name{position:absolute;top:160px;left:0;width:1200px;text-align:center;font-size:17px;font-weight:700;color:var(--blue)}
.quote-text{position:absolute;top:186px;left:400px;width:400px;text-align:center;font-size:13px;color:var(--muted);line-height:1.45}
.arrow{position:absolute;top:70px}
.arrow.prev{left:90px}.arrow.next{right:90px}

/* carriers */
.carriers{position:absolute;top:1870px;left:0;width:1200px}
.carrier-row{display:flex;justify-content:center;align-items:center;gap:70px;margin-top:48px}
.carrier{font-size:32px;font-weight:700;color:#c8102e}
.carrier.blue{color:var(--navy)}

/* footer */
.site-footer{position:absolute;top:2118px;left:0;width:1200px;height:114px;background:var(--blue);color:var(--white);text-align:center;padding:18px 200px}
.site-footer .label{font-size:13px;font-weight:700}
.site-footer p{font-size:12px;line-height:1.45;opacity:.9}
.site-footer .copy{margin-top:10px}
</style>
</head>
<body>

<header class="site-header">
  <div class="brand caps"><span>Insurance</span> Agent</div>
  <div class="header-phone">
    <svg width="26" height="26" viewBox="0 0 24 24"><circle cx="12" cy="12" r="12" fill="#1f5fae"/><path d="M8 6l2 0 1 3-1.5 1a7 7 0 0 0 4.5 4.5l1-1.5 3 1 0 2a2 2 0 0 1-2 2A10 10 0 0 1 6 8a2 2 0 0 1 2-2z" fill="#fff"/></svg>
    123 456 7890
  </div>
</header>

<section class="hero" role="img" aria-label="Business people in suits holding black umbrellas">
  <div class="hero-band">
    <h1>BUSINESS INSURANCE</h1>
    <span class="btn">GET A QUOTE!</span>
  </div>
</section>

<section class="quote-card">
  <aside class="agent">
    <div class="agent-photo" role="img" aria-label="Portrait of the insurance agent"></div>
    <div class="agent-name caps">Lorem Ipsum Dolor</div>
    <div class="agent-contact">
      <svg width="14" height="14" viewBox="0 0 24 24"><path d="M6 3l4 0 2 5-3 2a11 11 0 0 0 5 5l2-3 5 2 0 4a2 2 0 0 1-2 2A18 18 0 0 1 4 5a2 2 0 0 1 2-2z" fill="#1f5fae"/></svg>
      123 456 7890
    </div>
    <div class="agent-contact">
      <svg width="14" height="12" viewBox="0 0 24 18"><rect x="1" y="1" width="22" height="16" fill="none" stroke="#1f5fae" stroke-width="2"/><path d="M1 1l11 9 11-9" fill="none" stroke="#1f5fae" stroke-width="2"/></svg>
      info@agentsite.com
    </div>
    <p class="agent-note">Lorem ipsum dolor sit amet, consectetur adipiscing elit sed do eiusmod tempor incididunt labore.</p>
  </aside>
  <form class="quote-form">
    <h2 class="caps">Get An Instant <b>Insurance Quote.</b></h2>
    <div class="form-grid">
      <div class="field"><label>Full Name *</label><div class="input"></div></div>
      <div class="field"><label>Agent Name *</label><div class="input"></div></div>
      <div class="field"><label>Zip *</label><div class="input">Select</div></div>
      <div class="field"><label>Coverage Type *</label><div class="input">Select</div></div>
      <div class="field"><label>Date of Birth *</label><div class="dob"><div class="input">Month</div><div class="input">Day</div><div class="input">Year</div></div></div>
      <div class="field"><label>Phone *</label><div class="input"></div></div>
      <div class="field"><label>Current Policy *</label><div class="input">Select</div></div>
      <div class="field"><label>Email *</label><div class="input"></div></div>
    </div>
    <div class="btn submit">SUBMIT</div>
  </form>
</section>

<section class="about">
  <h2 class="section-title caps"><span>About</span> Insurance Agent</h2>
  <div class="rule"></div>
  <p>Lorem ipsum dolor sit amet, consectetur adipiscing elit, sed do eiusmod tempor incididunt ut labore et dolore magna aliqua. Ut enim ad minim veniam, quis nostrud exercitation ullamco laboris nisi ut aliquip ex ea commodo consequat. Duis aute irure dolor in reprehenderit in voluptate velit esse cillum dolore eu fugiat nulla pariatur. Excepteur sint occaecat cupidatat non proident, sunt in culpa qui officia deserunt mollit anim id est laborum sed perspiciatis.</p>
</section>

<section class="products">
  <h2 class="section-title caps"><span>Our</span> Insurance Products</h2>
  <div class="rule"></div>
  <div class="product-grid">
    <div class="product">
      <svg viewBox="0 0 90 80" width="90"><g fill="#1f5fae"><rect x="10" y="28" width="34" height="32"/><rect x="16" y="14" width="22" height="16" fill="none" stroke="#1f5fae" stroke-width="4"/><rect x="52" y="6" width="5" height="56"/><rect x="57" y="54" width="26" height="5"/><circle cx="18" cy="66" r="8"/><circle cx="44" cy="66" r="8"/></g></svg>
      <h3>LIFT</h3>
      <p>Lorem ipsum dolor sit amet, consectetur adipiscing elit sed do eiusmod tempor.</p>
      <span class="btn">GET A QUOTE!</span>
    </div>
    <div class="product">
      <svg viewBox="0 0 100 80" width="100"><g fill="#1f5fae"><path d="M22 18h56l10 22h6v26H6V40h6z"/><circle cx="26" cy="66" r="9"/><circle cx="74" cy="66" r="9"/></g><path d="M27 24h46l7 16H20z" fill="#fff"/></svg>
      <h3>AUTO</h3>
      <p>Lorem ipsum dolor sit amet, consectetur adipiscing elit sed do eiusmod tempor.</p>
      <span class="btn">GET A QUOTE!</span>
    </div>
    <div class="product">
      <svg viewBox="0 0 90 80" width="90"><path d="M45 4L4 40h12v36h58V40h12z" fill="#1f5fae"/><rect x="38" y="50" width="14" height="26" fill="#fff"/></svg>
      <h3>HOME</h3>
      <p>Lorem ipsum dolor sit amet, consectetur adipiscing elit sed do eiusmod tempor.</p>
      <span class="btn">GET A QUOTE!</span>
    </div>
    <div class="product">
      <svg viewBox="0 0 90 80" width="90"><rect x="30" y="8" width="30" height="14" fill="none" stroke="#1f5fae" stroke-width="5"/><rect x="6" y="20" width="78" height="54" rx="4" fill="#1f5fae"/><rect x="6" y="42" width="78" height="4" fill="#fff"/></svg>
      <h3>BUSINESS</h3>
      <p>Lorem ipsum dolor sit amet, consectetur adipiscing elit sed do eiusmod tempor.</p>
      <span class="btn">GET A QUOTE!</span>
    </div>
  </div>
</section>

<section class="testimonials">
  <h2 class="section-title caps"><span>Client</span> Testimonials</h2>
  <div class="rule"></div>
  <div class="people">
    <svg class="arrow prev" width="24" height="44" viewBox="0 0 24 44"><path d="M20 2L4 22l16 20" fill="none" stroke="#9aa1ab" stroke-width="3"/></svg>
    <div class="person side left" role="img" aria-label="Client portrait"></div>
    <div class="person main" role="img" aria-label="Featured client portrait"></div>
    <div class="person side right" role="img" aria-label="Client portrait"></div>
    <svg class="arrow next" width="24" height="44" viewBox="0 0 24 44"><path d="M4 2l16 20L4 42" fill="none" stroke="#9aa1ab" stroke-width="3"/></svg>
    <div class="quote-name caps">Lorem Ipsum Dolor Sit</div>
    <p class="quote-text">Lorem ipsum dolor sit amet, consectetur adipiscing elit, sed do eiusmod tempor incididunt ut labore et dolore magna aliqua.</p>
  </div>
</section>

<section class="carriers">
  <h2 class="section-title caps"><span>Insurance</span> Company</h2>
  <div class="rule"></div>
  <div class="carrier-row">
    <div class="carrier">Oakline</div>
    <div class="carrier blue">Harborview</div>
    <div class="carrier blue">Keystone Mutual</div>
    <div class="carrier blue">Fieldcrest</div>
  </div>
</section>

<footer class="site-footer">
  <div class="label">Disclaimer :</div>
  <p>Lorem ipsum dolor sit amet, consectetur adipiscing elit, sed do eiusmod tempor incididunt ut labore et dolore magna aliqua. Ut enim ad minim veniam, quis nostrud exercitation ullamco laboris nisi ut aliquip ex ea commodo consequat duis aute.</p>
  <p class="copy">Copyright © 2015 Insurance Agent &nbsp;|&nbsp; All rights reserved</p>
</footer>

</body>
</html>
```